Web Design for Two by Two Organic Soap Company

We need a website design for the company Brevin Organics based on the package design per attached.

The design should communicate high end, luxury organic. The site will provide facts about how the spread of disease causes deaths and can be prevented with hand washing. The site will also have a page about why we are passionate about organics and how that relates to our skin including skin facts.
Also, the site should have an e-commerce product page and shopping cart.

Target Market(s)

Educated, health conscious and socially conscious consumers who shop luxury. Target vendors include Marlow Grocers and Tavelli..

Industry/Entity Type

E-Commerce

Font styles to use
Other font styles liked:
• See attached

Requirements
Must have
• Use of Ying Yang leaf Logo provided.
Based on design provided.

```html
<!DOCTYPE html>
<html lang="en">
<head>
<meta charset="utf-8">
<title>Brevin Organics – Organic Soap</title>
<link href="https://fonts.googleapis.com/css2?family=Oswald:wght@300;400&family=Open+Sans:wght@400;600&display=swap" rel="stylesheet">
<style>
:root{
  --bg:#f3f3f3;
  --panel:#ffffff;
  --green:#6e9a0e;
  --lime:#8fbc1c;
  --olive:#2f3517;
  --olive-light:#5b6b1e;
  --text:#3c3c3c;
  --muted:#666;
  --line:#cfcfcf;
  --price:#d0251b;
  --sky:#cfe6f4;
}
*{box-sizing:border-box;margin:0;padding:0}
html,body{width:1023px;height:1200px;overflow:hidden;background:var(--bg)}
body{position:relative;font-family:"Oswald",sans-serif;font-weight:300;color:var(--text)}
.abs{position:absolute}
.header-scene{left:426px;top:0;width:597px;height:128px;background:linear-gradient(90deg,var(--bg) 0%,var(--sky) 35%,#d8ecf6 70%,#e4f0d2 100%);}
.header-scene::after{content:"";position:absolute;left:0;right:0;bottom:0;height:40px;background:linear-gradient(180deg,rgba(160,200,70,0),rgba(150,195,60,.55));}
.logo{left:85px;top:13px;width:262px;height:81px}
.logo-mark{position:absolute;left:0;top:0;width:53px;height:81px;background:var(--green)}
.logo-name{position:absolute;left:56px;top:0;width:206px;height:38px;background:var(--olive);color:#e7e3c8;font-size:26px;line-height:38px;padding-left:8px;}
.logo-tag{position:absolute;left:64px;top:44px;color:var(--olive-light);font-size:27px;letter-spacing:1px}
.nav{left:85px;top:125px;width:853px;height:38px;border-top:1px solid #9a9a9a;border-bottom:1px solid #9a9a9a;background:linear-gradient(#fafafa,#efefef)}
.nav a{position:absolute;top:0;line-height:36px;font-size:14px;letter-spacing:1px;color:#333;text-decoration:none;transform:translateX(-50%)}
.nav a.active::before{content:"";position:absolute;left:-14px;right:-14px;top:-1px;height:3px;background:var(--green)}
.box{background:var(--panel);box-shadow:0 8px 10px -8px rgba(0,0,0,.25)}
.box-title{position:absolute;left:0;right:0;top:0;height:38px;border-top:1px solid var(--green);border-bottom:3px double #9bbd5a;font-size:14px;padding:10px 0 0 17px;color:#222;background:var(--bg)}
.cart{left:85px;top:186px;width:222px;height:198px}
.cart .row{position:absolute;left:17px;right:14px;font-size:11px;color:var(--muted);border-bottom:1px solid #e3e3e3;height:28px;line-height:28px}
.cart b{color:var(--green);font-weight:400}
.btn{position:absolute;height:35px;border:1px solid #cfcfcf;background:#f5f5f5;padding:3px}
.btn span{display:block;height:100%;background:linear-gradient(#8cbc1e,#5a8a0a);color:#fff;font-size:16px;text-align:center;line-height:27px;letter-spacing:1px}
.shop{left:85px;top:411px;width:222px;height:204px}
.shop ul{position:absolute;left:17px;right:14px;top:50px;list-style:none}
.shop li{font-size:10.5px;color:var(--muted);height:26px;line-height:26px;border-bottom:1px solid #e3e3e3;padding-left:13px;position:relative}
.shop li::before{content:"";position:absolute;left:2px;top:10px;border:3px solid transparent;border-left:4px solid var(--green)}
.video-rule{left:85px;top:644px;width:222px;border-top:1px solid var(--green)}
.video{left:85px;top:656px;width:224px;height:172px;background:radial-gradient(circle at 55% 45%,#d9c4b4,#8a7b74 60%,#3e3e44)}
.video-bar{left:91px;top:796px;width:212px;height:24px;background:rgba(20,20,20,.6)}
.play{position:absolute;left:12px;top:6px;border:6px solid transparent;border-left:10px solid #fff}
.video-time{position:absolute;left:38px;top:-9px;font-family:"Open Sans",sans-serif;font-size:7px;background:#222;color:#fff;padding:0 2px}
.video-track{position:absolute;left:40px;top:10px;width:112px;height:4px;background:#777}
.video-hd{position:absolute;right:16px;top:4px;font-family:"Open Sans",sans-serif;font-size:10px;font-weight:600;color:#3ab0ff}
.video-foot{left:85px;top:842px;width:222px;height:10px}
.slider{left:325px;top:186px;width:613px;height:351px;border:1px solid #ddd}
.slide-green{left:338px;top:199px;width:250px;height:328px;background:linear-gradient(160deg,#7ea313,#92b51c 60%,#a6c534)}
.slide-photo{left:588px;top:199px;width:337px;height:328px;background:linear-gradient(135deg,#f6eee8,#e8b39a 45%,#f7f3ee 70%,#d8e6a8)}
.slide-circle{left:342px;top:318px;width:144px;height:144px;border-radius:50%;background:radial-gradient(circle at 40% 50%,#e8c8a0,#b79a8a 50%,#6d5b82)}
.slide-title{left:355px;top:222px;font-size:17px;color:#fff;font-weight:400}
.slide-text{left:354px;top:246px;width:205px;font-size:10px;line-height:15px;color:#f1f6dc}
.slide-text em{font-style:normal;color:#d7e79a}
.slide-more{left:355px;top:298px;font-size:11px;color:#2d3a0a;letter-spacing:1px}
.slide-caption{left:388px;top:491px;font-size:21px;color:#fff;word-spacing:2px;white-space:nowrap;text-shadow:0 1px 2px rgba(60,80,10,.5)}
.dots{left:873px;top:545px;display:flex;gap:6px}
.dots i{width:8px;height:8px;border-radius:50%;background:var(--green)}
.dots i:first-child{background:#fff;border:1px solid #ddd}
.feature-title{left:339px;top:569px;font-family:"Open Sans",sans-serif;font-size:13px;font-weight:400;color:#222}
.feature-rule{left:325px;top:593px;width:613px;border-top:1px solid #aaa}
.products{left:325px;top:597px;width:613px;height:253px;display:flex;gap:2px;background:#eee}
.product{position:relative;flex:1;background:var(--panel)}
.product-img{position:absolute;left:15px;top:17px;width:135px;height:100px;border:1px solid #8ab12d}
.product-name{position:absolute;left:22px;top:130px;font-size:13px;color:#333}
.product-price{position:absolute;left:22px;top:158px;font-size:13px;color:#333}
.product-price b{color:var(--price);font-weight:400;font-size:14px}
.product .btn{left:15px;top:196px;width:117px}
.about-title{left:98px;top:876px;font-size:15px;font-weight:300;color:#222}
.about-rule{left:86px;top:903px;width:852px;border-top:1px solid #999}
.about-text{left:88px;top:916px;width:848px;font-family:"Open Sans",sans-serif;font-size:10.3px;line-height:13.5px;color:#444;letter-spacing:.2px}
.about-list{left:88px;top:976px;list-style:none;font-family:"Open Sans",sans-serif;font-size:10.3px;color:#444}
.about-list li{height:20.5px;padding-left:9px;position:relative}
.about-list li::before{content:"";position:absolute;left:0;top:3px;border:3px solid transparent;border-left:4px solid var(--green)}
.more{left:96px;top:1039px;font-family:"Open Sans",sans-serif;font-size:8.5px;font-weight:600;color:var(--green)}
.footer-scene{left:0;top:1066px;width:1023px;height:134px;background:linear-gradient(180deg,var(--bg) 0%,#d2e7f3 30%,#b8d87a 62%,#7aa628 100%)}
.footer-links{left:0;width:1023px;top:1143px;text-align:center;font-size:10px;color:#1e2a08;letter-spacing:.5px}
.footer-links span{margin:0 6px}
.social{left:0;width:1023px;top:1172px;text-align:center;font-size:12px;font-weight:400;color:#fff}
.social span{margin:0 9px}
</style>
</head>
<body>
<div class="abs header-scene" role="img" aria-label="Illustrated sky with clouds, green hills and young trees"></div>

<div class="abs logo">
  <div class="logo-mark"></div>
  <div class="logo-name">Brevin Organics</div>
  <div class="logo-tag">organic soap</div>
</div>

<nav class="abs nav">
  <a class="active" href="#" style="left:89px">HOME</a>
  <a href="#" style="left:251px">ABOUT</a>
  <a href="#" style="left:409px">CONTACT</a>
  <a href="#" style="left:563px">STORES</a>
  <a href="#" style="left:735px">NATURAL SOAP</a>
</nav>

<section class="abs box cart">
  <div class="box-title">Your Shoping</div>
  <div class="row" style="top:50px">My Cart : <b>0</b> products</div>
  <div class="row" style="top:82px">Organic bar soaps</div>
  <div class="row" style="top:112px;border:0">Total : <b>$ 0</b></div>
  <div class="btn" style="left:53px;top:147px;width:117px"><span>Details</span></div>
</section>

<section class="abs box shop">
  <div class="box-title">Shop Online</div>
  <ul>
    <li>organic bar soaps</li>
    <li>castile liquid soaps</li>
    <li>organic balms &amp; oils</li>
    <li>unique handmade gifts</li>
    <li>timber &amp; coal for men</li>
  </ul>
</section>

<div class="abs video-rule"></div>
<div class="abs video" role="img" aria-label="Video still of a woman washing her face with soap lather"></div>
<div class="abs video-bar">
  <i class="play"></i><span class="video-time">03:27</span><i class="video-track"></i><span class="video-hd">HD</span>
</div>
<div class="abs box video-foot"></div>

<section class="abs box slider"></section>
<div class="abs slide-green" role="img" aria-label="Green backdrop with soft soap bars"></div>
<div class="abs slide-photo" role="img" aria-label="Photo of hands lathering with soap"></div>
<div class="abs slide-circle" role="img" aria-label="Soap bars with lavender"></div>
<div class="abs slide-title">NEW RELEASES</div>
<p class="abs slide-text">Sed ut perspiciatis unde omnis iste <em>natus</em> error sit voluptatem accusantium doloremque <em>laudantium</em>, totam rem aperiam</p>
<div class="abs slide-more">Read more</div>
<div class="abs slide-caption">Suitable For Face ,Hair and Skin &nbsp; Scented with Organic Essential Oils</div>
<div class="abs dots"><i></i><i></i><i></i><i></i><i></i></div>

<h2 class="abs feature-title">Feature Product</h2>
<div class="abs feature-rule"></div>
<section class="abs products">
  <article class="product">
    <div class="product-img" role="img" aria-label="Soap bars with lavender sprigs" style="background:linear-gradient(135deg,#f4efe8,#c9a98a 50%,#7a5f8a)"></div>
    <div class="product-name">organic bar soaps</div>
    <div class="product-price">Price : <b>$20</b></div>
    <div class="btn"><span>Buy</span></div>
  </article>
  <article class="product">
    <div class="product-img" role="img" aria-label="Stacked cream soap bars" style="background:linear-gradient(135deg,#fbfaf5,#f1dca0 55%,#d9c7a2)"></div>
    <div class="product-name">organic bar soaps</div>
    <div class="product-price">Price : <b>$20</b></div>
    <div class="btn"><span>Buy</span></div>
  </article>
  <article class="product">
    <div class="product-img" role="img" aria-label="Essential oil bottle with orange flowers" style="background:linear-gradient(135deg,#6b3a10,#e58a1c 50%,#f4e7c8)"></div>
    <div class="product-name">organic bar soaps</div>
    <div class="product-price">Price : <b>$20</b></div>
    <div class="btn"><span>Buy</span></div>
  </article>
  <article class="product">
    <div class="product-img" role="img" aria-label="Herbal soap bars" style="background:linear-gradient(160deg,#f7eeb8,#d8c76a 55%,#ecebd4)"></div>
    <div class="product-name">organic bar soaps</div>
    <div class="product-price">Price : <b>$20</b></div>
    <div class="btn"><span>Buy</span></div>
  </article>
</section>

<h2 class="abs about-title">About</h2>
<div class="abs about-rule"></div>
<p class="abs about-text">Lorem ipsum dolor sit amet, consectetur adipiscing elit. Nulla at dui vitae metus fringilla congue eget et libero. Vivamus lobortis, metus placerat euismod dictum, justo purus eleifend leo, ac imperdiet ipsum dui at mauris.Pellentesque volutpat adipiscing tristique. Nullam varius felis lorem, nec adipiscing nisi. In nisl ipsum, aliquet sit amet auctor nec, facilisis ac dolor. Fusce pulvinar volutpat leo, eu iaculis leo rutrum eu. Nullam ultrices ultrices massa, a sollicitudin elit lobortis eget. Integer id rutrum velit. Nam pellentesque scelerisque felis non tempus.</p>
<ul class="abs about-list">
  <li>Lorem ipsum dolor sit amet, consectetur adipiscing elit.</li>
  <li>Nulla at dui vitae metus fringilla congue egeteto purus emperdiet ipsum dui at mauris.</li>
  <li>Lorem ipsum dolor sit arus emperdiet ipsuonsectetur adipiscing elit.</li>
</ul>
<div class="abs more">- MORE INFO -</div>

<div class="abs footer-scene" role="img" aria-label="Illustrated green hills with young trees under a pale sky"></div>
<div class="abs footer-links"><span>HOME</span>|<span>ABOUT</span>|<span>CONTACT</span>|<span>STORES</span>|<span>NATURAL SOAP</span></div>
<div class="abs social"><span>Friendwall</span><span>Linkpath</span><span>Viewtube</span></div>
</body>
</html>
```